Volbrey Inc Business Card

Looking to get an updated business card for a Contract Machining company (www.volbreyinc.example) - looking for a clean design the portrays the technical nature of the business - colors can follow the website design and be in any combination that makes sense (red black, white, metallic or silver) - logos attached for use also. Would like space for: Name, title, business phone (555 214-3086), cell phone , website (www.volbreyinc.example) - possibly QR code could be integrated for website (designer choice), business address - 418 Harlow Bend, Ashcombe, WI 53199 (cards will be for 4 employees, I will either need to modify a template or I can provide individual information)
Target Market(s)
Aerospace, defense and medical device manufacturing companies that need machining
Industry/Entity Type
Machining for aerospace, defense, medical
Contact Information for Business Card
Name, Title, Business Phone, Cell Phone, email, business website and business address
Look and feel

```html
<!DOCTYPE html>
<html lang="en">
<head>
<meta charset="utf-8">
<title>Volbrey Inc Business Card</title>
<link rel="stylesheet" href="https://fonts.googleapis.com/css2?family=Poppins:wght@400;700;800&display=swap">
<style>
  :root {
    --bg: #adadad;
    --ink: #121212;
    --red: #b01e24;
    --white: #ffffff;
    --light: #e6e6e6;
  }
  * { margin: 0; padding: 0; box-sizing: border-box; }
  html, body { width: 1093px; height: 1200px; overflow: hidden; background: var(--bg); }
  body { position: relative; font-family: "Poppins", sans-serif; }

  .card { position: absolute; left: 264px; width: 580px; height: 357px; overflow: hidden; }
  .card-front { top: 226px; background: var(--ink); }
  .card-back { top: 620px; background: var(--red); }

  .front-shape { position: absolute; inset: 0; }

  .name-marker { position: absolute; left: 0; top: 43px; width: 18px; height: 32px; background: var(--red); }
  .person-name { position: absolute; left: 30px; top: 42px; font-size: 21px; font-weight: 700; color: var(--red); line-height: 1; text-transform: uppercase; letter-spacing: 0.2px; }
  .person-title { position: absolute; left: 29px; top: 61px; font-size: 17px; font-weight: 400; color: var(--light); line-height: 1.2; }

  .address { position: absolute; left: 27px; top: 121px; font-size: 17px; color: var(--light); line-height: 21px; font-style: normal; }

  .contact-list { position: absolute; left: 29px; top: 218px; list-style: none; }
  .contact-list li { display: flex; align-items: center; height: 21px; font-size: 15px; color: var(--light); white-space: nowrap; }
  .contact-list svg { width: 15px; height: 15px; margin-right: 7px; flex: none; }
  .contact-list .accent { color: var(--red); }

  .brand-name { position: absolute; font-weight: 800; line-height: 1; text-transform: uppercase; }
  .brand-front { left: 280px; width: 280px; top: 162px; text-align: center; font-size: 34px; color: var(--ink); letter-spacing: 1px; }
  .brand-back { left: 0; width: 100%; top: 130px; text-align: center; font-size: 88px; color: var(--white); letter-spacing: 1px; }
</style>
</head>
<body>

<section class="card card-front" aria-label="Business card front">
  <svg class="front-shape" width="580" height="357" viewBox="0 0 580 357" aria-hidden="true">
    <circle cx="420" cy="178.5" r="178" fill="var(--red)"/>
    <rect x="420" y="0" width="160" height="357" fill="var(--red)"/>
    <circle cx="420" cy="178.5" r="140" fill="none" stroke="var(--ink)" stroke-width="5"/>
  </svg>

  <div class="name-marker"></div>
  <h1 class="person-name">Daniel Archer</h1>
  <p class="person-title">Managing Director</p>

  <address class="address">418 Harlow Bend<br>Ashcombe, WI 53199</address>

  <ul class="contact-list">
    <li>
      <svg viewBox="0 0 24 24" aria-hidden="true"><path fill="var(--red)" d="M6.6 10.8a15.1 15.1 0 0 0 6.6 6.6l2.2-2.2a1 1 0 0 1 1-.25 11.4 11.4 0 0 0 3.6.57 1 1 0 0 1 1 1V20a1 1 0 0 1-1 1A17 17 0 0 1 3 4a1 1 0 0 1 1-1h3.5a1 1 0 0 1 1 1c0 1.25.2 2.45.57 3.57a1 1 0 0 1-.25 1z"/></svg>
      555 214-3086
    </li>
    <li>
      <svg viewBox="0 0 24 24" aria-hidden="true"><rect x="6" y="2" width="12" height="20" rx="2" fill="none" stroke="var(--red)" stroke-width="2"/><circle cx="12" cy="18.5" r="1" fill="var(--red)"/></svg>
      555 867-0192
    </li>
    <li>
      <svg viewBox="0 0 24 24" aria-hidden="true"><rect x="2" y="5" width="20" height="14" fill="var(--red)"/><path d="M2 5l10 8 10-8" fill="none" stroke="var(--ink)" stroke-width="1.5"/></svg>
      info@volbreyinc.example
    </li>
    <li>
      <svg viewBox="0 0 24 24" aria-hidden="true"><g fill="none" stroke="var(--red)" stroke-width="1.8"><circle cx="12" cy="12" r="9.5"/><ellipse cx="12" cy="12" rx="4" ry="9.5"/><path d="M2.5 12h19M4 7h16M4 17h16"/></g></svg>
      <span>www.<span class="accent">volbreyinc</span>.example</span>
    </li>
  </ul>

  <p class="brand-name brand-front">Volbrey</p>
</section>

<section class="card card-back" aria-label="Business card back">
  <p class="brand-name brand-back">Volbrey</p>
</section>

</body>
</html>
```